Business Card Design Project

Doctor, Pain Management. Need a new business card design with appointment info on the back. New address is 18 Corvell Road, Suite 304, Brisdale, NJ 07391. Right now I believe the rest of the information is staying the same.

```html
<!DOCTYPE html>
<html lang="en">
<head>
<meta charset="utf-8">
<title>Harbor Pain Care – Business Card</title>
<link rel="stylesheet" href="https://fonts.googleapis.com/css2?family=Roboto:wght@400;500;700&family=Open+Sans:ital,wght@0,400;0,600;1,400&display=swap">
<style>
  :root{
    --bg:#d9d6d0;
    --card-dark:#1e1f22;
    --band-dark:#23221c;
    --sky:#6fd3f7;
    --lemon:#e8e33a;
    --white:#ffffff;
    --ink:#2a2a2a;
    --line:#8a8a8a;
  }
  *{box-sizing:border-box;margin:0;padding:0}
  html,body{width:1200px;height:911px;overflow:hidden;background:var(--bg)}
  body{position:relative;font-family:"Roboto",Arial,sans-serif}

  .card{position:absolute;width:580px;height:330px;box-shadow:0 10px 28px rgba(0,0,0,.28);overflow:hidden}

  /* Front */
  .card-front{left:110px;top:100px;background:var(--card-dark)}
  .card-front .wave{position:absolute;inset:0;width:100%;height:100%}
  .front-info{position:absolute;left:36px;top:74px;color:var(--white);white-space:nowrap}
  .doctor-name{font-size:23px;font-weight:500;color:var(--sky);letter-spacing:.2px}
  .doctor-title{font-size:15px;font-weight:500;color:var(--lemon);margin-top:3px}
  .contact{list-style:none;margin-top:14px;font-size:14.5px;line-height:1.38;color:#e6e6e6}

  /* Back */
  .card-back{left:510px;top:480px;background:var(--white)}
  .brand-band{position:absolute;left:0;top:0;width:100%;height:112px;background:var(--band-dark);
    display:flex;align-items:center;padding-left:40px;gap:14px}
  .brand-dot{width:22px;height:22px;border-radius:50%;background:var(--lemon)}
  .brand-name{font-family:"Open Sans",Arial,sans-serif;font-size:30px;font-weight:400;color:var(--lemon)}
  .form{position:absolute;left:40px;right:40px;top:134px;font-family:"Open Sans",Arial,sans-serif;color:var(--ink);font-size:15px}
  .field{display:flex;align-items:flex-end;gap:6px;margin-bottom:14px}
  .field .fill{flex:1;border-bottom:1.5px dotted var(--line);height:14px}
  .row{display:flex;gap:24px}
  .row .field{flex:1}
  .suffix{font-size:12px}
  .days{display:flex;justify-content:space-between;margin:4px 0 14px}
  .day{display:flex;align-items:center;gap:5px}
  .box{width:13px;height:13px;border:1.3px solid var(--ink)}
  .notice{font-style:italic;font-size:12px;text-align:center;line-height:1.4}
</style>
</head>
<body>

<section class="card card-front" aria-label="Business card front">
  <svg class="wave" viewBox="0 0 580 330" preserveAspectRatio="none" aria-hidden="true">
    <path d="M530 0 C450 70 480 170 440 250 C420 290 390 315 350 330 L580 330 L580 0 Z" fill="var(--sky)"/>
    <circle cx="500" cy="80" r="30" fill="none" stroke="var(--white)" stroke-width="5"/>
  </svg>
  <div class="front-info">
    <h1 class="doctor-name">MIRREN OKAFOR, M.D., PH.D.</h1>
    <p class="doctor-title">Board Certified Anesthesiologist</p>
    <ul class="contact">
      <li>18 Corvell Road</li>
      <li>Suite 304</li>
      <li>Brisdale, NJ 07391</li>
      <li>973.555.0148</li>
      <li>973.555.0162</li>
      <li>meridianpain.office@gmail.com</li>
      <li>www.harborpaincare.com</li>
    </ul>
  </div>
</section>

<section class="card card-back" aria-label="Business card back, appointment reminder">
  <div class="brand-band">
    <span class="brand-dot"></span>
    <span class="brand-name">Harbor Pain Care</span>
  </div>
  <div class="form">
    <div class="field"><span>Name :</span><span class="fill"></span></div>
    <div class="row">
      <div class="field"><span>Date:</span><span class="fill"></span></div>
      <div class="field"><span>Time :</span><span class="fill"></span><span class="suffix">AM/PM</span></div>
    </div>
    <div class="days">
      <span class="day">Sun <span class="box"></span></span>
      <span class="day">Mon <span class="box"></span></span>
      <span class="day">Tue <span class="box"></span></span>
      <span class="day">Wed <span class="box"></span></span>
      <span class="day">Thu <span class="box"></span></span>
      <span class="day">Fri <span class="box"></span></span>
      <span class="day">Sat <span class="box"></span></span>
    </div>
    <p class="notice">Please give me 24 hours notice if you are unable to keep your appointment or<br>a cancellation fee may be charged.</p>
  </div>
</section>

</body>
</html>
```